Maple Lantern Productions web site

I need to build a website for a new company I am launching next month. Maple Lantern Productions is a company based in New England that provides sound, lighting, and audio visual services to weddings, corporate, and any other cusomer base looking for quality service for a fair price. Looking for somebody to do a full site not just the image files. I am looking to keep the colors of my logo (orange and black) and possibly grey and white. I am looking to build my site very similar to brightvaleevents.example, which is owned by a friend of mine. I like how he has the big pictures that load in to the site and the basic menu items. I'll need a gallery of photos. The designs should communicate quality, value and trust.
My website address is maplelanternco.example.
Updates

Hi and thanks to everyone for posting such great ideas for our new design.I have some items that I'd like to ask you all to focus on in your revisions.I like how http://www.brightvaleevents.example/ website has five or six high res pictures that change in a slideshow format with a caption that loads in for each one for the different types of services. Try and capture pics like these and with teh same headings as he has. The basic menu designs have been interesting.I am more fond of the menus that are more white with some orange as I dont want it to be too dark. I'm curious to see how your galleries will work and if i'll be able to edit the pages myself? I have some more info on the company for you to fill in:website address is ciderhouseco.comemail: info@ciderhouseco.comaddress: Maple Lantern Productions57 Littlefield StreetAvon, MA 02417"New England's finest DJ's, lighting and sound, video and more. Creating memories one perfect event at a time."Put this under the loading pictures as a tagline.About Cider HouseCider House Productions is a collection of New England's finest talent, ready to make your next event the one you've dreamed of. We have the skills and expertise to deliver your vision of your perfect event. From elegant weddings to themed mitzvah's, corporate av, videography and detail lighting, we offer all of the elements to make your event a success. Added Wednesday, March 1, 2017

Designer's Please also make sure that your design flows well on any device it is being viewed on as well. Thanks. Added Wednesday, March 1, 2017

Project Deadline Extended Reason: Hello designerThank you all very much for your hard work on our project. Im sorry but i need to extend the date of my project. Our parent conpany Rook Nine Prodactions sponsors Bay Youth Assemblies and we are currently at their leadership conference on the Cape. I will be back in on Monday and with your help will get this finished by Thursday the 16th. Thanks Added Thursday, March 9, 2017

Project Deadline Extended Reason: One of the designers is not responding so I now have to make revisions with other designers. I hope to get this website done over the weekends so please get your revisions as soon as possible. Thank you. I am also upgrading the budget another $75 to hopefully get some more interest on my project. Added Wednesday, March 15, 2017

Target Market(s)

Wedding - Corporate -

Industry/Entity Type

It Company

Coding

Coded - Design and coding required

Number of Pages Required

5+ page

Font styles to use
Sans Serif

Requirements
Must have
• Photo Gallery - I want to be able to edit it myself
Nice to have
• I like the look of my friends website brightvaleevents.example

```html
<!DOCTYPE html>
<html lang="en">
<head>
<meta charset="utf-8">
<title>Maple Lantern Productions</title>
<link href="https://fonts.googleapis.com/css2?family=Montserrat:wght@500;600;700&family=Roboto:wght@300;400;500&display=swap" rel="stylesheet">
<style>
:root{
  --orange:#f26b2c;
  --orange-dark:#e0561a;
  --ink:#222222;
  --text:#555555;
  --muted:#777777;
  --line:#e3e3e3;
  --panel:#f5f6f8;
  --footer:#f1f1f1;
  --bar:#2b2b2b;
  --white:#ffffff;
}
*{box-sizing:border-box;margin:0;padding:0}
html,body{width:1200px;height:3442px;overflow:hidden}
body{font-family:"Roboto",Arial,sans-serif;color:var(--text);background:var(--white);position:relative}
section,header,footer{position:relative;width:1200px}
.abs{position:absolute}
.centered{left:0;right:0;text-align:center}

/* header */
.site-header{height:87px;background:var(--white)}
.brand{left:86px;top:18px;display:flex;align-items:center;gap:12px}
.brand-dot{width:50px;height:50px;border-radius:50%;background:var(--orange)}
.brand-name{font-family:"Montserrat",sans-serif;font-weight:700;font-size:17px;color:var(--ink);line-height:20px;letter-spacing:.5px}
.main-nav{left:490px;top:37px;display:flex;font-family:"Montserrat",sans-serif;font-weight:500;font-size:12px;color:var(--ink);text-transform:uppercase}
.main-nav span{position:absolute;white-space:nowrap}
.main-nav .active{color:var(--orange)}
.search-btn{left:1069px;top:24px;width:44px;height:44px;border-radius:50%;background:var(--orange)}

/* hero */
.hero{height:503px;background:
  radial-gradient(ellipse at 50% 35%,rgba(255,226,190,.55),transparent 60%),
  linear-gradient(180deg,#c8826b 0%,#b9675a 40%,#8a4a3e 70%,#5b2e28 100%)}
.hero-arrow{top:226px;width:50px;height:50px;border:2px solid rgba(255,255,255,.9);border-radius:50%}
.hero-arrow svg{position:absolute;left:14px;top:14px}
.hero-title{top:228px;font-weight:300;font-size:60px;color:var(--white);letter-spacing:1px}
.hero-text{top:314px;font-size:13px;line-height:23px;color:var(--white)}
.btn-outline{border:1.5px solid var(--white);color:var(--white);font-size:12px;text-transform:uppercase;display:flex;align-items:center;justify-content:center;font-family:"Montserrat",sans-serif}
.hero-btn{left:532px;top:379px;width:136px;height:37px}

/* welcome */
.welcome{height:271px}
.section-title{font-weight:400;font-size:27px;color:#444;text-transform:uppercase}
.section-title em{font-style:normal;color:var(--orange)}
.welcome .section-title{top:44px}
.welcome-text{top:94px;left:270px;width:660px;text-align:center;font-size:12px;line-height:25px}
.btn-solid{background:var(--orange);color:var(--white);font-family:"Montserrat",sans-serif;font-size:12px;font-weight:500;text-transform:uppercase;display:flex;align-items:center;justify-content:center;border-radius:2px}
.welcome-btn{left:521px;top:185px;width:159px;height:40px}

/* services */
.services{height:1441px;background:var(--panel)}
.services .section-title{top:32px}
.section-sub{font-size:12px}
.services .section-sub{top:76px}
.service-photo{width:418px;height:255px;border-radius:3px}
.service-title{font-family:"Montserrat",sans-serif;font-weight:600;font-size:16px;color:var(--ink);text-transform:uppercase}
.service-text{width:500px;font-size:11.5px;line-height:23px}
.service-btn{width:135px;height:46px}
.divider{left:103px;width:994px;height:1px;background:var(--line)}
.ph-sound{background:linear-gradient(160deg,#d89a5a 0%,#6b4a35 45%,#2c2420 100%)}
.ph-light{background:linear-gradient(160deg,#d9b7e8 0%,#8c5fc8 45%,#3c2a7a 100%)}
.ph-audio{background:linear-gradient(160deg,#7fa6d6 0%,#3f4f78 45%,#1a1c26 100%)}
.ph-visual{background:linear-gradient(135deg,#7c8a99 0%,#c9c3bd 45%,#4a3e3a 100%)}

/* about */
.about{height:275px;background:linear-gradient(180deg,#f3763b 0%,#ef6a2e 60%,#ea6a32 100%)}
.about .section-title{top:44px;color:var(--white);font-size:25px}
.about-text{top:94px;left:240px;width:720px;text-align:center;font-size:12px;line-height:25px;color:var(--white)}
.about-btn{left:487px;top:193px;width:227px;height:39px;font-family:"Roboto",sans-serif}

/* gallery */
.gallery{height:517px}
.gallery .section-title{top:44px}
.gallery .section-sub{top:86px}
.tile{border-radius:2px}
.g1{left:87px;top:124px;width:510px;height:165px;background:linear-gradient(120deg,#2a2a4a,#8a7d92 50%,#1d1d2e)}
.g2{left:606px;top:124px;width:248px;height:342px;background:linear-gradient(180deg,#2a2a26,#b79a4a 55%,#3a3a30)}
.g3{left:865px;top:124px;width:248px;height:165px;background:linear-gradient(180deg,#4a3d30,#e3d7c5 60%,#a8968a)}
.g4{left:87px;top:301px;width:250px;height:165px;background:linear-gradient(180deg,#8a5a34,#3e2a22)}
.g5{left:346px;top:301px;width:251px;height:165px;background:linear-gradient(150deg,#8a7766,#3a2e28)}
.g6{left:865px;top:301px;width:248px;height:165px;background:linear-gradient(150deg,#e8e8e8,#2a2a2a 60%,#6a5a40)}

/* footer */
.site-footer{height:280px;background:var(--footer)}
.footer-logo{left:87px;top:25px;width:280px;text-align:center}
.footer-dot{width:96px;height:96px;border-radius:50%;background:var(--orange);margin:0 auto 20px}
.footer-name{font-family:"Montserrat",sans-serif;font-weight:700;font-size:27px;line-height:30px;color:var(--ink);letter-spacing:1px}
.col-title{font-family:"Montserrat",sans-serif;font-weight:600;font-size:15px;color:var(--ink);text-transform:uppercase}
.contact-col{left:406px;top:50px}
.contact-list{list-style:none;margin-top:28px;font-size:11.5px;color:#444}
.contact-list li{display:flex;align-items:flex-start;gap:12px;height:29px}
.contact-list a{color:#444}
.news-col{left:650px;top:50px;width:220px}
.news-text{margin-top:26px;font-size:12px;line-height:19px;color:#444}
.news-input{margin-top:12px;width:212px;height:32px;border:1px solid #d6d6d6;background:var(--white);font-size:11px;color:var(--muted);padding:0 12px;display:flex;align-items:center}
.news-btn{margin-top:20px;width:82px;height:24px;font-size:10px}
.follow-col{left:909px;top:50px;width:200px}
.follow-text{margin-top:26px;font-size:11.5px;line-height:19px;color:var(--muted)}
.socials{margin-top:22px;display:flex;gap:8px}
.socials span{width:33px;height:33px;border-radius:50%;border:1.5px solid #b8b8b8}
.copyright{position:absolute;left:0;top:3374px;width:1200px;height:68px;background:var(--bar);color:#dddddd;font-size:12px;display:flex;align-items:center;justify-content:center}
</style>
</head>
<body>

<header class="site-header">
  <div class="brand abs"><span class="brand-dot"></span><span class="brand-name">MAPLE LANTERN<br>PRODUCTIONS</span></div>
  <nav class="main-nav abs">
    <span class="active" style="left:15px">Home</span>
    <span style="left:98px">About Us</span>
    <span style="left:203px">Services</span>
    <span style="left:306px">Events</span>
    <span style="left:398px">Gallery</span>
    <span style="left:499px">Contact Us</span>
  </nav>
  <div class="search-btn abs">
    <svg width="44" height="44" viewBox="0 0 44 44"><circle cx="20" cy="20" r="6" fill="none" stroke="#fff" stroke-width="2.2"/><line x1="24.5" y1="24.5" x2="29" y2="29" stroke="#fff" stroke-width="2.4" stroke-linecap="round"/></svg>
  </div>
</header>

<section class="hero" role="img" aria-label="Banquet hall set for a wedding reception with draped walls, white chair covers and tall floral centrepieces">
  <div class="hero-arrow abs" style="left:26px"><svg width="20" height="20" viewBox="0 0 20 20"><polyline points="13,3 6,10 13,17" fill="none" stroke="#fff" stroke-width="2.2"/></svg></div>
  <div class="hero-arrow abs" style="left:1124px"><svg width="20" height="20" viewBox="0 0 20 20"><polyline points="7,3 14,10 7,17" fill="none" stroke="#fff" stroke-width="2.2"/></svg></div>
  <h1 class="hero-title abs centered">MAPLE LANTERN</h1>
  <p class="hero-text abs centered">Sed ut perspiciatis unde omnis iste natus error sit voluptatem accusantium doloremque laudantium, totam rem<br>aperiam, eaque ipsa quae ab illo inventore veritatis et quasi architecto beatae vitae dicta sunt explicabo.</p>
  <div class="btn-outline hero-btn abs">Read More</div>
</section>

<section class="welcome">
  <h2 class="section-title abs centered">Welcome to <em>Maple Lantern Productions</em></h2>
  <p class="welcome-text abs">Sed ut perspiciatis unde omnis iste natus error sit voluptatem accusantium doloremque laudantium, totam rem aperiam, eaque ipsa quae ab illo inventore veritatis et quasi architecto beatae vitae dicta sunt explicabo. Nemo enim ipsam aut consequuntur magni dolores eos qui ratione voluptatem sequi nesciunt</p>
  <div class="btn-solid welcome-btn abs">Read More Info</div>
</section>

<section class="services">
  <h2 class="section-title abs centered">Our <em>Services</em></h2>
  <p class="section-sub abs centered">Sed ut perspiciatis unde omnis iste natus error sit voluptatem accusantium doloremque laudantium,</p>

  <div class="service-photo ph-sound abs" style="left:103px;top:135px" role="img" aria-label="Live band on a lit stage behind a sound mixing console"></div>
  <h3 class="service-title abs" style="left:583px;top:146px">Sound Services</h3>
  <p class="service-text abs" style="left:583px;top:200px">Sed ut perspiciatis unde omnis iste natus error sit voluptatem accusantium doloremque laudantium, totam rem aperiam, eaque ipsa quae ab illo inventore veritatis et quasi architecto beatae vitae dicta sunt explicabo. Nemo enim ipsam voluptatem quia voluptas sit aspernatur la consequuntur magni dolores eos qui ratione voluptatem sequi nesciunt.</p>
  <div class="btn-solid service-btn abs" style="left:585px;top:325px">Read More Info</div>
  <div class="divider abs" style="top:431px"></div>

  <h3 class="service-title abs" style="left:103px;top:481px">Lighting Services</h3>
  <p class="service-text abs" style="left:103px;top:535px">Sed ut perspiciatis unde omnis iste natus error sit voluptatem accusantium doloremque laudantium, totam rem aperiam, eaque ipsa quae ab illo inventore veritatis et quasi architecto beatae vitae dicta sunt explicabo. Nemo enim ipsam voluptatem quia voluptas sit aspernatur la consequuntur magni dolores eos qui ratione voluptatem sequi nesciunt.</p>
  <div class="btn-solid service-btn abs" style="left:105px;top:660px">Read More Info</div>
  <div class="service-photo ph-light abs" style="left:679px;top:470px" role="img" aria-label="Reception tent washed in purple uplighting with draped ceiling"></div>
  <div class="divider abs" style="top:766px"></div>

  <div class="service-photo ph-audio abs" style="left:103px;top:805px" role="img" aria-label="DJ controller and laptop with glowing pads"></div>
  <h3 class="service-title abs" style="left:583px;top:816px">Audio Services</h3>
  <p class="service-text abs" style="left:583px;top:870px">Sed ut perspiciatis unde omnis iste natus error sit voluptatem accusantium doloremque laudantium, totam rem aperiam, eaque ipsa quae ab illo inventore veritatis et quasi architecto beatae vitae dicta sunt explicabo. Nemo enim ipsam voluptatem quia voluptas sit aspernatur la consequuntur magni dolores eos qui ratione voluptatem sequi nesciunt.</p>
  <div class="btn-solid service-btn abs" style="left:585px;top:995px">Read More Info</div>
  <div class="divider abs" style="top:1101px"></div>

  <h3 class="service-title abs" style="left:103px;top:1151px">Visual Services</h3>
  <p class="service-text abs" style="left:103px;top:1205px">Sed ut perspiciatis unde omnis iste natus error sit voluptatem accusantium doloremque laudantium, totam rem aperiam, eaque ipsa quae ab illo inventore veritatis et quasi architecto beatae vitae dicta sunt explicabo. Nemo enim ipsam voluptatem quia voluptas sit aspernatur la consequuntur magni dolores eos qui ratione voluptatem sequi nesciunt.</p>
  <div class="btn-solid service-btn abs" style="left:105px;top:1330px">Read More Info</div>
  <div class="service-photo ph-visual abs" style="left:679px;top:1140px" role="img" aria-label="Collage of wedding photography prints"></div>
</section>

<section class="about" role="img" aria-label="Orange-tinted banquet hall backdrop">
  <h2 class="section-title abs centered">About Us</h2>
  <p class="about-text abs">Sed ut perspiciatis unde omnis iste natus error sit voluptatem accusantium doloremque laudantium, totam rem aperiam, eaque ipsa quae ab illo inventore veritatis et quasi architecto beatae vitae dicta sunt explicabo. Nemo enim ipsam voluptatem quia voluptas sit sed quia consequuntur magni dolores eos qui ratione voluptatem sequi nesciunt</p>
  <div class="btn-outline about-btn abs">Click Here for More Info</div>
</section>

<section class="gallery">
  <h2 class="section-title abs centered">Photo <em>Gallery</em></h2>
  <p class="section-sub abs centered">Sed ut perspiciatis unde omnis iste natus error sit voluptatem accusantium doloremque laudantium,</p>
  <div class="tile g1 abs" role="img" aria-label="Couple's first dance framed by sparkler fountains"></div>
  <div class="tile g2 abs" role="img" aria-label="Garden walkway under arches of string lights"></div>
  <div class="tile g3 abs" role="img" aria-label="Reception tables beneath hanging lights"></div>
  <div class="tile g4 abs" role="img" aria-label="Band performing on stage"></div>
  <div class="tile g5 abs" role="img" aria-label="Guitarist playing at an event"></div>
  <div class="tile g6 abs" role="img" aria-label="Saxophone player in a suit"></div>
</section>

<footer class="site-footer">
  <div class="footer-logo abs">
    <div class="footer-dot"></div>
    <div class="footer-name">MAPLE LANTERN<br>PRODUCTIONS</div>
  </div>
  <div class="contact-col abs">
    <h4 class="col-title">Contact Us</h4>
    <ul class="contact-list">
      <li><svg width="14" height="14" viewBox="0 0 14 14"><rect x="1" y="3" width="12" height="9" rx="1" fill="#777"/><rect x="3" y="1" width="8" height="3" fill="#777"/></svg>(000)-121-1231 (Phone)</li>
      <li><svg width="14" height="14" viewBox="0 0 14 14"><rect x="1" y="4" width="12" height="8" rx="1" fill="#777"/><rect x="4" y="1" width="6" height="4" fill="#777"/></svg>(000)-121-1231 (Fax)</li>
      <li><svg width="14" height="14" viewBox="0 0 14 14"><rect x="1" y="3" width="12" height="9" fill="#777"/><polyline points="1,3 7,8 13,3" fill="none" stroke="#fff" stroke-width="1.2"/></svg><a>info@maplelanternco.example</a></li>
      <li><svg width="14" height="14" viewBox="0 0 14 14"><path d="M7 1a4 4 0 0 1 4 4c0 3-4 8-4 8S3 8 3 5a4 4 0 0 1 4-4z" fill="#777"/><circle cx="7" cy="5" r="1.5" fill="#fff"/></svg><span>#24 Lorem Ipsum Dummy<br>Lorem Ipsum</span></li>
    </ul>
  </div>
  <div class="news-col abs">
    <h4 class="col-title">Newsletter</h4>
    <p class="news-text">Register Your email address to get information ablout us</p>
    <div class="news-input">Email Address</div>
    <div class="btn-solid news-btn">Subscribe</div>
  </div>
  <div class="follow-col abs">
    <h4 class="col-title">Follow Us</h4>
    <p class="follow-text">Lorem ipsum dolor sit amet, conse ctetur adipisicing elit. Nulla in purus nibh. Donec ornare</p>
    <div class="socials"><span></span><span></span><span></span><span></span><span></span></div>
  </div>
</footer>

<div class="copyright">© Copyright 2017 Maple Lantern co.All Rights Reserved</div>

</body>
</html>
```